TV Antenna Installation business needs a unique flyer

We need a simple but effective flyer design for our TV Aerial installation company based in Newcastle, NSW, Australia called Bright Harbour TV & Aerial Svcs.
We are trying to target areas where there has been a new transmitter installed and most houses just require their aerial redirecting and tv's retuning.

Industry/Entity Type

Business

Requirements
Must have
• We would like the idea of a headline phrase such as " Poor TV reception……..now a thing from the past" or something similar & catchy.
Also "Did you know a new transmitter has been recently installed in your area, we can therefore now GUARANTEE 100% PERFECT PICTURE
Charges from only $95.
- Free 5 year warranty
- Free signal testing
- Free Onsite Quote
Phone 0463 527 209
Nice to have
• Other services include:

- New Installs
- Extra Points & repairs
- TV wall mounting/Home Cinema
- Pull down tall masts

Modern tv picture, see example uploaded

```html
<!DOCTYPE html>
<html lang="en">
<head>
<meta charset="utf-8">
<title>Bright Harbour TV &amp; Aerial Svcs – Flyer</title>
<link rel="stylesheet" href="https://fonts.googleapis.com/css2?family=Bree+Serif&family=Open+Sans:ital,wght@0,400;0,700;1,400&display=swap">
<style>
  :root {
    --green: #2db670;
    --orange: #f7931e;
    --white: #ffffff;
    --tv-dark: #5e5a55;
    --tv-light: #b9b3aa;
  }
  * { box-sizing: border-box; margin: 0; padding: 0; }
  html, body { width: 897px; height: 1200px; overflow: hidden; }
  body { background: var(--green); font-family: "Open Sans", Arial, sans-serif; color: var(--white); }

  .flyer { position: relative; width: 897px; height: 1200px; background: var(--green); }

  .brand-tab { position: absolute; top: 0; left: 0; width: 897px; height: 143px; }

  .call-block {
    position: absolute; left: 45px; top: 28px;
    font-family: "Bree Serif", Georgia, serif; font-size: 38px; line-height: 48px;
  }
  .call-block .phone { display: flex; align-items: center; gap: 6px; }
  .call-block svg { width: 30px; height: 30px; }

  .brand-name {
    position: absolute; left: 420px; top: 44px; width: 460px; text-align: center;
    font-family: "Bree Serif", Georgia, serif; font-size: 54px; line-height: 60px;
    color: var(--orange); white-space: nowrap;
  }

  .tv-photo {
    position: absolute; left: 62px; top: 237px; width: 415px; height: 257px; border-radius: 10px;
    background: linear-gradient(135deg, var(--tv-light), var(--tv-dark));
  }

  .headline {
    position: absolute; left: 500px; top: 200px; width: 380px;
    font-family: "Bree Serif", Georgia, serif; font-size: 76px; line-height: 78px; text-align: center;
  }
  .headline .small { font-size: 68px; }
  .subhead {
    position: absolute; left: 505px; top: 405px; width: 380px; text-align: center;
    font-family: "Bree Serif", Georgia, serif; font-size: 50px; line-height: 60px;
  }

  .intro {
    position: absolute; left: 62px; top: 540px; width: 777px;
    font-size: 33px; line-height: 49px; text-align: justify; text-align-last: justify;
    letter-spacing: -0.6px;
  }
  .intro strong { font-weight: 700; }

  .offer {
    position: absolute; left: 93px; top: 727px; width: 709px; height: 255px;
    background: var(--orange); border: 3px dashed var(--white); text-align: center;
  }
  .offer h2 {
    font-family: "Bree Serif", Georgia, serif; font-weight: 400; font-size: 54px; line-height: 62px;
    margin-top: 14px;
  }
  .offer ul { list-style: none; margin-top: 16px; font-style: italic; font-size: 29px; line-height: 44px; }

  .services-title { position: absolute; left: 62px; top: 1010px; font-weight: 700; font-size: 31px; }
  .services {
    position: absolute; left: 45px; top: 1062px; width: 820px;
    list-style: none; display: grid; grid-template-columns: 342px 1fr;
    font-size: 26px; line-height: 38px;
  }
  .services li { display: flex; align-items: center; gap: 6px; }
  .services svg { width: 22px; height: 22px; flex: none; }
</style>
</head>
<body>
<main class="flyer">
  <svg class="brand-tab" viewBox="0 0 897 143" aria-hidden="true">
    <polygon points="380,0 897,0 897,143 445,143" fill="#ffffff"/>
  </svg>

  <div class="call-block">
    <div>Call Us Today</div>
    <div class="phone">
      <svg viewBox="0 0 30 30" aria-hidden="true">
        <circle cx="15" cy="15" r="13" fill="none" stroke="#fff" stroke-width="2"/>
        <path d="M10 8 l3 0 l1 4 l-2 1.5 q1.5 3.5 4.5 4.5 l1.5 -2 l4 1 l0 3 q-1 1.5 -3 1.5 q-9 -1 -10.5 -10.5 q0 -2 1.5 -3z" fill="#fff"/>
      </svg>
      <span>0463 527 209</span>
    </div>
  </div>

  <div class="brand-name">bright harbour</div>

  <div class="tv-photo" role="img" aria-label="Vintage television set showing a static-filled screen"></div>

  <h1 class="headline">Poor TV<br><span class="small">reception</span></h1>
  <p class="subhead">NOW a thing<br>from the past</p>

  <p class="intro">Did you know a new transmitter has been recently installed in your area, we can therefore now <strong>GUARANTEED 100% PERFECT PICTURE</strong></p>

  <section class="offer">
    <h2>Charges from only $95</h2>
    <ul>
      <li>+ Free 5 years warranty</li>
      <li>+ Free signal testing</li>
      <li>+ Free Onsite Quote</li>
    </ul>
  </section>

  <h3 class="services-title">Other services include:</h3>
  <ul class="services">
    <li><svg viewBox="0 0 22 22" aria-hidden="true"><path d="M3 12 l5 5 l11 -12" fill="none" stroke="#fff" stroke-width="3"/></svg>New Installs</li>
    <li><svg viewBox="0 0 22 22" aria-hidden="true"><path d="M3 12 l5 5 l11 -12" fill="none" stroke="#fff" stroke-width="3"/></svg>TV wall mounting/Home Cinema</li>
    <li><svg viewBox="0 0 22 22" aria-hidden="true"><path d="M3 12 l5 5 l11 -12" fill="none" stroke="#fff" stroke-width="3"/></svg>Extra Points &amp; repairs</li>
    <li><svg viewBox="0 0 22 22" aria-hidden="true"><path d="M3 12 l5 5 l11 -12" fill="none" stroke="#fff" stroke-width="3"/></svg>Pull down tall masts</li>
  </ul>
</main>
</body>
</html>
```